Medical group practice

We need a flyer design incorporating the three doctors in the practice, there is a general practitioner, ophthalmologist and an obstetrician & Gynaecologist. see the attached file for the concept. will leave the colour design up to you

Target Market(s)

general public

Industry/Entity Type

Health Care

Colors

Designer to choose colors to be used in the design.

Requirements
Must have
• logos included in attachement

```html
<!DOCTYPE html>
<html lang="en">
<head>
<meta charset="utf-8">
<title>Crestview Medical Flyer</title>
<link rel="stylesheet" href="https://fonts.googleapis.com/css2?family=Montserrat:wght@800&family=Source+Sans+3:wght@300;400;600;700&display=swap">
<style>
:root{
  --red:#e01f26;
  --red-dark:#c8232a;
  --ink:#1e1e1e;
  --muted:#6a6a6a;
  --rule:#c9c9c9;
  --navy:#1c3a5a;
  --stage:#434343;
  --teal-1:#8fd0dc;
  --teal-2:#5c98a4;
  --teal-3:#b9dde3;
}
*{box-sizing:border-box;margin:0;padding:0}
html,body{width:1200px;height:1200px;overflow:hidden;background:var(--stage)}
body{font-family:"Source Sans 3",sans-serif;color:var(--ink)}
.flyer{position:absolute;left:180px;top:10px;width:841px;height:1179px;background:#fff;overflow:hidden}
.top-bar{position:absolute;left:0;top:0;width:100%;height:15px;background:#a9a9a9}
.brand{position:absolute;left:0;top:56px;width:100%;text-align:center}
.brand-name{display:inline-flex;align-items:center;gap:12px;font-family:"Montserrat",sans-serif;font-weight:800;font-size:36px;color:var(--red);letter-spacing:.5px}
.brand-dot{width:30px;height:30px;border-radius:50%;background:var(--red)}
.tagline{display:block;margin-top:4px;font-weight:400;font-size:29px;color:#6e6e6e}
.hero{position:absolute;left:0;top:158px;width:100%;height:360px;background:linear-gradient(100deg,var(--teal-1) 0%,var(--teal-3) 45%,#9cc4cb 70%,var(--teal-2) 100%)}
.photo{position:absolute;top:430px;width:176px;height:176px;border-radius:50%;border:6px solid var(--red);box-shadow:0 0 0 3px #fff}
.photo-1{left:45px;background:linear-gradient(135deg,#d8e6ee,#6fb6d8 60%,#2f6f9a)}
.photo-2{left:332px;background:linear-gradient(135deg,#eef2f4,#8fb3d6 55%,#3c5f8a)}
.photo-3{left:606px;background:linear-gradient(135deg,#f1e9e6,#b9b7c8 55%,#535879)}
.partner{position:absolute;top:640px;width:170px;text-align:center;font-weight:600;font-size:15px;padding-bottom:10px;border-bottom:1.5px solid var(--navy)}
.partner-1{left:50px;color:#5b2a7a}
.partner-2{left:337px;color:var(--navy)}
.partner-3{left:611px;color:var(--navy)}
.doctor{position:absolute;top:698px;width:262px;border-left:1px solid var(--rule);padding-left:9px;height:190px}
.doctor-1{left:17px}
.doctor-2{left:289px}
.doctor-3{left:567px}
.doctor h2{font-weight:700;font-size:19px;color:var(--red);line-height:1.1}
.doctor .role{font-weight:400;font-size:14px;color:var(--muted);line-height:1.25}
.doctor .services{margin-top:20px;font-size:14px;line-height:24.6px}
.doctor-3 .services{margin-top:6px;line-height:18.5px;text-align:justify}
.email{position:absolute;top:880px;display:flex;align-items:center;gap:10px;font-size:13.5px}
.email-1{left:26px}.email-2{left:296px}.email-3{left:576px}
.email svg{width:19px;height:14px}
.contact-band{position:absolute;left:0;top:929px;width:100%;height:161px;background:linear-gradient(90deg,var(--red-dark),var(--red) 50%,var(--red-dark))}
.contact-tab{position:absolute;left:352px;top:915px;width:137px;height:49px;background:linear-gradient(#fafafa,#cfcfcf);font-size:24px;text-align:center;line-height:49px;color:var(--ink)}
.contact-item{position:absolute;top:975px;width:260px;text-align:center;color:#fff;font-size:15.5px;line-height:1.05}
.contact-item svg{display:block;margin:0 auto 10px;width:40px;height:40px}
.ci-1{left:8px}
.ci-2{left:290px;font-size:21px}
.ci-2 svg{margin-bottom:14px}
.ci-3{left:572px}
.footer{position:absolute;left:0;top:1090px;width:100%;height:89px;background:linear-gradient(#e9e9e9,#fafafa 50%,#dedede);text-align:center;font-size:12.3px;line-height:89px;color:var(--ink)}
</style>
</head>
<body>
<main class="flyer">
  <div class="top-bar"></div>
  <header class="brand">
    <span class="brand-name"><span class="brand-dot"></span>CRESTVIEW MEDICAL</span>
    <span class="tagline">Your Health is our Priority</span>
  </header>

  <div class="hero" role="img" aria-label="Doctor with stethoscope touching a digital heart-rate display"></div>

  <div class="photo photo-1" role="img" aria-label="Patient having an eye examination"></div>
  <div class="photo photo-2" role="img" aria-label="General practitioner consulting with a patient"></div>
  <div class="photo photo-3" role="img" aria-label="Patient receiving an ultrasound scan"></div>

  <div class="partner partner-1">Clearsight Eye Services</div>
  <div class="partner partner-2">Whitfield Family Care</div>
  <div class="partner partner-3">Mehra Women's Health</div>

  <section class="doctor doctor-1">
    <h2>Dr. Lucia E. Fernandez</h2>
    <p class="role">MD. Surgeon Ophthalmologist</p>
    <p class="services">Eyes disease examination,<br>Surgery of Pterygium, Cataract,<br>Glaucoma, Emergency: Conjunctivitis,<br>Traumatism, Foreign body and more</p>
  </section>
  <section class="doctor doctor-2">
    <h2>Dr. Marcus Whitfield, MD.</h2>
    <p class="role">General Practitioner</p>
    <p class="services">General Checks, Annual Check ups<br>WoundCare/Dressings,Incision&amp;Draiage<br>Suturing lacerations, Pain Injections<br>Glucose checks, Foreign Body Removal</p>
  </section>
  <section class="doctor doctor-3">
    <h2>Dr. Arjun Mehra</h2>
    <p class="role">BMedSci, MBBS, DM (O&amp;G), FACOG<br>Obstetrician &amp; Gynaecologist</p>
    <p class="services">Obstetrics - Prenatal Care, Delivery, Postnatal checks, High Risk pregnancy Gynaecology - Pap smears, Abnormal vaginal bleeding, Fibroids, Colpos-copy, Family planning, Infertility, Cancer screening, And More….</p>
  </section>

  <p class="email email-1"><svg viewBox="0 0 19 14"><rect width="19" height="14" fill="#e01f26"/><path d="M0 0l9.5 7L19 0M0 14l7-6M19 14l-7-6" stroke="#fff" stroke-width="1.4" fill="none"/></svg>lucia.fernandez@mailbox.test</p>
  <p class="email email-2"><svg viewBox="0 0 19 14"><rect width="19" height="14" fill="#e01f26"/><path d="M0 0l9.5 7L19 0M0 14l7-6M19 14l-7-6" stroke="#fff" stroke-width="1.4" fill="none"/></svg>marcus.whitfield@mailbox.test</p>
  <p class="email email-3"><svg viewBox="0 0 19 14"><rect width="19" height="14" fill="#e01f26"/><path d="M0 0l9.5 7L19 0M0 14l7-6M19 14l-7-6" stroke="#fff" stroke-width="1.4" fill="none"/></svg>drmehra@mailbox.test</p>

  <section class="contact-band">
  </section>
  <div class="contact-tab">Contact Us</div>

  <div class="contact-item ci-1">
    <svg viewBox="0 0 40 40"><path d="M20 2a13 13 0 0 0-13 13c0 10 13 23 13 23s13-13 13-23A13 13 0 0 0 20 2z" fill="#fff"/><circle cx="20" cy="15" r="5" fill="#e01f26"/></svg>
    42 Harbour Road, Port Elms,<br>St. Avila
  </div>
  <div class="contact-item ci-2">
    <svg viewBox="0 0 40 40"><circle cx="20" cy="20" r="18" fill="none" stroke="#fff" stroke-width="2.5"/><path d="M13 12c1-1 3-1 4 0l2 3c.6 1 .3 2-.5 2.7l-1 .8c1 2.4 2.6 4 5 5l.8-1c.7-.8 1.8-1 2.7-.5l3 2c1 1 1 3 0 4-2 2-5 2-8 0-3.5-2-6-4.5-8-8-2-3-2-6 0-8z" fill="#fff"/></svg>
    (555) 310 2240 / 2241
  </div>
  <div class="contact-item ci-3">
    <svg viewBox="0 0 40 40"><circle cx="20" cy="20" r="19" fill="#fff"/><path d="M20 9v11l6 6" stroke="#e01f26" stroke-width="3" fill="none" stroke-linecap="round"/></svg>
    Monday – Fridays 9am-6pm<br>Saturdays 10am – 5pm
  </div>

  <footer class="footer">General Practitioner - (555) 310 4417 / &nbsp; Ophthalmologist - (555) 310 5582 / &nbsp; Obstetrician/ Gynaecologist (555) 310 6630, (555) 310 7194</footer>
</main>
</body>
</html>
```